Past Every River Oz Tour Flyer

I need a dynamic flyer for a concert tour.
I have uploaded the file. Please use these ingredients for the design.
The font for the title is Jellyka Jellyfish lower case from www.glyphbarn.example
Updates
We are getting close!! We just need bright colours, the headings to STAND OUT and Byron Bay has to be moved to under NSW Bellingen.
Thanks for all your hard work!
Target Market(s)
We are targeting a wide range of customers from old age to children and families
Industry/Entity Type
Tour
Look and feel
Each slider illustrates characteristics of the customer's brand and the style your logo design should communicate.

```html
<!DOCTYPE html>
<html lang="en">
<head>
<meta charset="utf-8">
<title>Past Every River – Australia Tour</title>
<link rel="stylesheet" href="https://fonts.googleapis.com/css2?family=Sacramento&family=Fjalla+One&family=Yanone+Kaffeesatz:wght@400;600&family=Open+Sans:wght@400&display=swap">
<style>
  :root {
    --ink: #070508;
    --night: #1d0f2c;
    --dusk: #4a1a4f;
    --sun: #f2a32b;
    --ember: #c7381d;
    --red: #e0201c;
    --orange: #f39a1e;
    --gold: #f7e600;
    --teal: #127a86;
    --white: #ffffff;
    --box: #ec8a1e;
  }
  * { margin: 0; padding: 0; box-sizing: border-box; }
  html, body { width: 829px; height: 1200px; overflow: hidden; background: var(--ink); }
  .flyer { position: relative; width: 829px; height: 1200px; overflow: hidden; background: var(--ink); }

  .hero-photo {
    position: absolute; inset: 0 0 204px 0;
    background:
      radial-gradient(ellipse 220px 380px at 400px 340px, rgba(243,163,43,.85), rgba(199,56,29,.55) 55%, transparent 80%),
      radial-gradient(ellipse 160px 300px at 720px 330px, rgba(199,56,29,.6), transparent 75%),
      radial-gradient(circle 180px at 60px 200px, rgba(242,163,43,.35), transparent 80%),
      linear-gradient(180deg, var(--dusk) 0%, var(--night) 45%, var(--ink) 100%);
  }
  .mosaic {
    position: absolute; left: 0; right: 0; top: 560px; height: 436px;
    background:
      radial-gradient(ellipse 200px 240px at 120px 260px, rgba(18,122,134,.75), transparent 75%),
      radial-gradient(ellipse 220px 260px at 360px 230px, rgba(224,32,28,.65), transparent 75%),
      radial-gradient(ellipse 220px 240px at 640px 200px, rgba(20,110,70,.6), transparent 75%),
      linear-gradient(180deg, transparent 0%, rgba(60,20,70,.35) 40%, rgba(7,5,8,.2) 100%);
  }

  .title {
    position: absolute; left: 60px; top: 70px;
    font-family: "Sacramento", cursive; font-weight: 400;
    color: var(--white); line-height: .95;
    text-shadow: 0 2px 8px rgba(0,0,0,.5);
  }
  .title .line-1 { display: block; font-size: 118px; padding-left: 70px; }
  .title .line-2 { display: block; font-size: 132px; }

  .choir-name, .tour-name {
    position: absolute; font-family: "Fjalla One", sans-serif;
    -webkit-text-stroke: 2px var(--white); paint-order: stroke fill;
    text-shadow: 2px 3px 4px rgba(0,0,0,.6);
    letter-spacing: -.5px;
  }
  .choir-name { left: 52px; top: 332px; font-size: 46px; color: var(--red); }
  .tour-name { left: 178px; top: 402px; font-size: 50px; color: var(--orange); }

  .stops { font-family: "Open Sans", sans-serif; color: var(--white); }
  .region { position: absolute; }
  .region h2 {
    font-family: "Yanone Kaffeesatz", sans-serif; font-weight: 600;
    font-size: 36px; color: var(--gold); line-height: 1; margin-bottom: 12px;
  }
  .region ul { list-style: none; font-size: 19px; line-height: 30px; }
  .region.vic { left: 128px; top: 660px; }
  .region.act { left: 128px; top: 884px; }
  .region.nsw { left: 315px; top: 660px; }
  .region.qld { left: 547px; top: 736px; }

  .tickets {
    position: absolute; left: 0; top: 996px; width: 418px; height: 204px;
    background: var(--box); color: var(--white);
    font-family: "Yanone Kaffeesatz", sans-serif; font-weight: 400;
    font-size: 30px; line-height: 28px; text-align: center;
    padding-top: 22px;
  }
  .partners {
    position: absolute; left: 418px; top: 996px; right: 0; height: 204px;
    background: var(--ink);
    display: flex; align-items: center; justify-content: space-around;
    font-family: "Yanone Kaffeesatz", sans-serif; font-weight: 600;
    font-size: 28px; color: var(--white);
  }
  .partner { display: flex; align-items: center; gap: 10px; }
  .partner .dot { width: 22px; height: 22px; border-radius: 50%; background: var(--red); }
</style>
</head>
<body>
<main class="flyer">
  <div class="hero-photo" role="img" aria-label="Photo of young dancers in yellow and red costumes with grass skirts against a starry purple night sky"></div>
  <div class="mosaic" role="img" aria-label="Colourful triangle mosaic pattern in teal, red, purple and green"></div>

  <h1 class="title"><span class="line-1">Past Every</span><span class="line-2">River</span></h1>
  <p class="choir-name">The Savanna Youth Choir</p>
  <p class="tour-name">Australia Tour</p>

  <section class="stops">
    <div class="region vic">
      <h2>VICTORIA</h2>
      <ul><li>Geelong</li><li>Sunbury</li><li>Melbourne</li><li>Bendigo</li><li>Albury</li></ul>
    </div>
    <div class="region act">
      <h2>A.C.T.</h2>
      <ul><li>Canberra</li></ul>
    </div>
    <div class="region nsw">
      <h2>N.S.W.</h2>
      <ul><li>Nowra</li><li>Sydney</li><li>Wollongong</li><li>Blue Mountains</li><li>Port Macquarie</li><li>Laurieton</li><li>Taree</li><li>Bellingen</li><li>Byron Bay</li></ul>
    </div>
    <div class="region qld">
      <h2>QLD</h2>
      <ul><li>Gold Coast</li><li>Sunshine Coast</li><li>Brisbane</li></ul>
    </div>
  </section>

  <footer>
    <div class="tickets">
      TICKETS and info at<br>
      www.songbridge.example<br>
      CONTACT:<br>
      Dana Whitlow&nbsp; 0400 555 019
    </div>
    <div class="partners">
      <div class="partner"><span class="dot"></span><span>Songbridge</span></div>
      <div class="partner"><span>Savanna Youth Choir</span></div>
    </div>
  </footer>
</main>
</body>
</html>
```